PWRPT design for Company

Project: Develop a pwrpt for Brightwell. This can be just a blank pwrpt with standard templates that we can use to build our content and solutions around.
Website: www.qt7lx.example
Color Pallet: Try to use the color schema from our website.
PWRPT Design Tips: While we are a research-based company, our primary target is schools and school districts. We say our work is RESEARCH, POLICY, AND PRACTICE. I would like images that represent “WHY” our research matters, i.e. students, teachers, and administrators. If you can use images and stock photos that represent students with diverse backgrounds, teachers that are diverse and clearly teaching, and administrators that run a school, university, etc. We are in the process of updating our website, but the color scheme will remain the same.
Additional Information:
We built, researched, and designed, www.brvo-kt.example .
We built, researched, and designed, http://67pwgamma.example/olar/index.html
Target Market(s)
EDUCATION
Industry/Entity Type
It Company
Look and feel

```html
<!DOCTYPE html>
<html lang="en">
<head>
<meta charset="utf-8">
<title>Brightwell Presentation Templates</title>
<link href="https://fonts.googleapis.com/css2?family=Montserrat:wght@400;500;700;800&family=Lato:wght@400;700;900&display=swap" rel="stylesheet">
<style>
  :root{
    --coral:#f2673f;
    --sun:#f9d24a;
    --amber:#ee7c13;
    --slate:#4b5b5a;
    --ink:#3a3a3a;
    --body:#3f3f3f;
    --paper:#ffffff;
    --stage:#000000;
    --photo-warm:#c89a7a;
    --photo-deep:#5b3a2c;
  }
  *{margin:0;padding:0;box-sizing:border-box}
  html,body{width:1200px;height:2192px;overflow:hidden;background:var(--stage)}
  body{position:relative;font-family:"Montserrat",Arial,sans-serif;color:var(--body)}
  .slide{position:absolute;background:var(--paper);overflow:hidden}
  .slide--one{left:19px;top:19px;width:1162px;height:657px}
  .slide--three{left:19px;top:714px;width:1162px;height:657px}
  .slide--welcome{left:95px;top:1415px;width:1007px;height:758px}

  .accent-bar{position:absolute;left:38px;top:0;width:439px;height:6px;background:var(--sun)}
  .slide-title{position:absolute;left:38px;top:30px;font-weight:800;font-size:41px;letter-spacing:-.5px;color:var(--ink);line-height:1.2}
  .slide-title span{color:var(--coral)}

  .brand{position:absolute;display:flex;flex-direction:column;align-items:flex-end}
  .brand__row{display:flex;align-items:center;gap:10px}
  .brand__mark{width:20px;height:20px;background:var(--coral)}
  .brand__name{font-family:"Lato",Arial,sans-serif;font-weight:400;color:var(--slate);font-size:34px;line-height:1}
  .brand__tag{font-family:"Lato",Arial,sans-serif;font-size:8px;letter-spacing:.8px;color:var(--slate);margin-top:5px}
  .slide .brand--header{right:16px;top:30px}

  .decor{position:absolute;left:0;top:0;pointer-events:none}

  .footer-band{position:absolute;left:0;bottom:0;width:100%;height:27px;background:var(--slate);color:#fff;font-size:12px;line-height:27px;padding-left:10px}

  .col-title{font-weight:700;font-size:26px;color:var(--coral);line-height:1.2}
  .col-text{font-size:14.5px;line-height:28px;color:var(--body)}

  .single-col{position:absolute;left:54px;top:134px;width:461px}
  .single-col .col-text{text-align:justify;hyphens:auto;-webkit-hyphens:auto;margin-top:0}
  .single-col .col-text + .col-text{margin-top:28px}
  .feature-photo{position:absolute;left:0;top:0}

  .tri-col{position:absolute;top:166px;width:320px;text-align:center}
  .tri-col svg{display:block;margin:0 auto}
  .tri-col .col-title{margin-top:14px}
  .tri-col .col-text{margin-top:2px;padding:0 22px}
  .tri-col--a{left:71px}
  .tri-col--b{left:412px}
  .tri-col--c{left:753px}

  .welcome-art{position:absolute;left:0;top:0}
  .welcome-copy{position:absolute;left:672px;top:442px;color:#fff}
  .welcome-copy h1{font-weight:800;font-size:44px;line-height:1.1;letter-spacing:-.5px}
  .welcome-copy .program{font-family:"Lato",Arial,sans-serif;font-size:26px;margin-top:12px}
  .welcome-copy .date{font-family:"Lato",Arial,sans-serif;font-size:22px;margin-top:10px}
  .welcome-legal{position:absolute;left:32px;top:662px;width:580px;font-family:"Lato",Arial,sans-serif;font-size:13.5px;line-height:21px;color:var(--ink)}
  .brand--welcome{right:36px;top:646px}
  .brand--welcome .brand__name{font-size:52px}
  .brand--welcome .brand__mark{width:30px;height:30px}
  .brand--welcome .brand__tag{font-size:12px;margin-top:6px}
  .welcome-base{position:absolute;left:0;bottom:0;width:100%;height:19px;background:var(--slate)}
</style>
</head>
<body>

<section class="slide slide--one">
  <div class="accent-bar"></div>
  <svg class="decor" width="1162" height="657" aria-hidden="true">
    <path d="M0 105 C180 160 260 380 170 657" fill="none" stroke="var(--sun)" stroke-opacity=".35" stroke-width="1.5"/>
  </svg>
  <h2 class="slide-title">ONE <span>COL CONTENT</span></h2>
  <div class="brand brand--header">
    <div class="brand__row"><span class="brand__mark"></span><span class="brand__name">Brightwell</span></div>
    <span class="brand__tag">INSIGHT • GUIDANCE • ACTION</span>
  </div>
  <div class="single-col">
    <h3 class="col-title">Col Title</h3>
    <p class="col-text">Lorem Ipsum is simply dummy text of the printing and typesetting industry. Lorem Ipsum has been the industry's standard dummy text ever since the 1500s, when an unknown printer took a galley of type and scrambled it to make a type specimen book. It has survived not only five centuries, but also the leap into electronic typesetting, remaining essentially unchanged. Lorem Ipsum is simply dummy text of the printing and typesetting industry.</p>
    <p class="col-text">Lorem Ipsum has been the industry's standard dummy text ever since the 1500s, when an unknown printer took a galley of type and scrambled it to make a type specimen book. It has survived not only five centuries, but also the leap into electronic typesetting, remaining essentially unchanged.</p>
  </div>
  <svg class="feature-photo" width="1162" height="657">
    <defs>
      <radialGradient id="groupTone" cx="50%" cy="45%" r="60%">
        <stop offset="0" stop-color="var(--photo-warm)"/>
        <stop offset="1" stop-color="var(--photo-deep)"/>
      </radialGradient>
    </defs>
    <circle cx="830" cy="363" r="202" fill="none" stroke="var(--coral)" stroke-opacity=".7" stroke-width="1.5"/>
    <circle cx="830" cy="363" r="189" fill="url(#groupTone)" role="img" aria-label="Photo of three smiling students sharing an open book"/>
    <circle cx="730" cy="191" r="17" fill="var(--sun)"/>
    <circle cx="971" cy="500" r="20" fill="var(--coral)"/>
  </svg>
  <div class="footer-band">Copyright @Text</div>
</section>

<section class="slide slide--three">
  <div class="accent-bar"></div>
  <svg class="decor" width="1162" height="657" aria-hidden="true">
    <defs>
      <linearGradient id="triTone" x1="0" y1="0" x2="1" y2="1">
        <stop offset="0" stop-color="#9a6c5a"/>
        <stop offset="1" stop-color="#3f5a8a"/>
      </linearGradient>
    </defs>
    <circle cx="1000" cy="330" r="300" fill="none" stroke="var(--coral)" stroke-opacity=".3" stroke-width="1.5"/>
    <path d="M700 0 C820 40 900 80 1162 60" fill="none" stroke="var(--sun)" stroke-opacity=".4" stroke-width="1.5"/>
    <circle cx="876" cy="100" r="10" fill="var(--sun)"/>
  </svg>
  <h2 class="slide-title">3 <span>COL CONTENT</span></h2>
  <div class="brand brand--header">
    <div class="brand__row"><span class="brand__mark"></span><span class="brand__name">Brightwell</span></div>
    <span class="brand__tag">INSIGHT • GUIDANCE • ACTION</span>
  </div>
  <div class="tri-col tri-col--a">
    <svg width="296" height="253"><polygon points="148,14 282,239 14,239" fill="url(#triTone)" stroke="url(#triTone)" stroke-width="24" stroke-linejoin="round" role="img" aria-label="Photo of a student reading a tablet with classmates"/></svg>
    <h3 class="col-title">Col Title Text here</h3>
    <p class="col-text">Lorem Ipsum is simply dummy text of the printing and typesetting industry. Lorem Ipsum has been the industry's standard dummy text ever since the 1500s,</p>
  </div>
  <div class="tri-col tri-col--b">
    <svg width="296" height="253"><polygon points="14,14 282,14 148,239" fill="url(#triTone)" stroke="url(#triTone)" stroke-width="24" stroke-linejoin="round" role="img" aria-label="Photo of a student seated at a classroom desk looking up"/></svg>
    <h3 class="col-title">Col Title Text here</h3>
    <p class="col-text">Lorem Ipsum is simply dummy text of the printing and typesetting industry. Lorem Ipsum has been the industry's standard dummy text ever since the 1500s,</p>
  </div>
  <div class="tri-col tri-col--c">
    <svg width="296" height="253"><polygon points="148,14 282,239 14,239" fill="url(#triTone)" stroke="url(#triTone)" stroke-width="24" stroke-linejoin="round" role="img" aria-label="Photo of a smiling young man on campus"/></svg>
    <h3 class="col-title">Col Title Text here</h3>
    <p class="col-text">Lorem Ipsum is simply dummy text of the printing and typesetting industry. Lorem Ipsum has been the industry's standard dummy text ever since the 1500s,</p>
  </div>
  <div class="footer-band">Copyright @Text</div>
</section>

<section class="slide slide--welcome">
  <svg class="welcome-art" width="1007" height="619">
    <defs>
      <linearGradient id="crowdTone" x1="0" y1="0" x2="1" y2="1">
        <stop offset="0" stop-color="#d9d3cc"/>
        <stop offset=".45" stop-color="#8a6450"/>
        <stop offset="1" stop-color="#3a3634"/>
      </linearGradient>
    </defs>
    <rect x="0" y="0" width="1007" height="619" fill="url(#crowdTone)" role="img" aria-label="Photo of a diverse group of smiling students holding notebooks"/>
    <polygon points="829,0 1007,0 1007,619 568,619" fill="var(--amber)"/>
    <line x1="829" y1="0" x2="568" y2="619" stroke="var(--slate)" stroke-width="12"/>
  </svg>
  <div class="welcome-copy">
    <h1>WELCOME</h1>
    <p class="program">Route2Futures (R2F)</p>
    <p class="date">August 21st, 2017</p>
  </div>
  <p class="welcome-legal">© 2017 All rights reserved. Contains confidential and proprietary information and may not be disclosed or reproduced without the prior written consent of Brightwell</p>
  <div class="brand brand--welcome">
    <div class="brand__row"><span class="brand__mark"></span><span class="brand__name">Brightwell</span></div>
    <span class="brand__tag">INSIGHT • GUIDANCE • ACTION</span>
  </div>
  <div class="welcome-base"></div>
</section>

</body>
</html>
```